Maple Roster Business Card for recruitment company

We are looking for a Business Card Design that incorporates our personal details and our busines name and logo. We are a specialized search consultancy that recruit Property and Construction professionals.
We would like a business card that stands out and is appealing to the Construction and Property industry as well.

Target Market(s)

people in the construction and property industry

Contact Information for Business Card

Business Name and logo

Font styles to use
Serif

Colors
0094D4
00A9DD
6FCCEA
C7EBF8
E9F6FB

Requirements
Must have
• Business name and logo as well as contact details
Should not have
• No photos of us please

```html
<!DOCTYPE html>
<html lang="en">
<head>
<meta charset="utf-8">
<title>Maple Roster – Business Card</title>
<link rel="stylesheet" href="https://fonts.googleapis.com/css2?family=Josefin+Sans:wght@300&family=Roboto:wght@400;500&display=swap">
<style>
  :root {
    --ink: #003f55;
    --text-grey: #5c6268;
    --paper: #ffffff;
    --page: #ffffff;
    --shadow: rgba(0, 0, 0, 0.18);
  }
  * { box-sizing: border-box; margin: 0; padding: 0; }
  html, body { width: 687px; height: 1200px; overflow: hidden; background: var(--page); }
  body { position: relative; font-family: "Roboto", Arial, sans-serif; }

  .card {
    position: absolute;
    left: 63px;
    width: 560px;
    height: 320px;
    background: var(--paper);
    box-shadow: 0 1px 6px var(--shadow);
    overflow: hidden;
  }
  .card--front { top: 250px; }
  .card--back { top: 620px; }

  .wordmark {
    font-family: "Josefin Sans", "Century Gothic", sans-serif;
    font-weight: 300;
    color: var(--ink);
    white-space: nowrap;
    letter-spacing: 0.02em;
  }
  .card--front .wordmark {
    position: absolute;
    top: 128px; left: 0; right: 0;
    text-align: center;
    font-size: 54px;
    line-height: 1;
  }

  .band { position: absolute; left: 0; width: 100%; }
  .band svg { display: block; width: 100%; height: 100%; }
  .band__text {
    position: absolute; inset: 0;
    display: flex; flex-direction: column; align-items: center; justify-content: center;
    color: #fff;
  }
  .card--front .band { top: 244px; height: 43px; }
  .band__url { font-size: 19px; font-weight: 500; letter-spacing: 0.12em; }

  .card--back .band { top: 246px; height: 54px; }
  .band__sector { font-size: 17px; line-height: 1.1; }
  .band__kind { font-size: 10.5px; letter-spacing: 0.32em; margin-top: 3px; }

  .social { position: absolute; top: 38px; left: 51px; display: flex; gap: 6px; }
  .social__dot { width: 22px; height: 22px; border-radius: 50%; }
  .social__dot--mail { background: #111; }
  .social__dot--network { background: #1b86c8; }

  .person { position: absolute; top: 36px; left: 311px; color: var(--text-grey); }
  .person__name { font-size: 19px; font-weight: 500; line-height: 1.1; }
  .person__role { font-size: 12px; margin-top: 3px; }

  .contacts { position: absolute; top: 112px; left: 311px; list-style: none; color: var(--text-grey); font-size: 12.5px; }
  .contacts li { display: flex; align-items: center; gap: 12px; margin-bottom: 7px; line-height: 1.15; }
  .contacts svg { flex: none; width: 17px; height: 17px; }

  .card--back .wordmark {
    position: absolute; top: 194px; left: 32px;
    font-size: 33px; line-height: 1;
  }
</style>
</head>
<body>

<section class="card card--front" aria-label="Business card front">
  <div class="wordmark">MAPLE ROSTER</div>
  <div class="band">
    <svg viewBox="0 0 560 43" preserveAspectRatio="none" aria-hidden="true">
      <rect width="560" height="43" fill="var(--ink)"/>
      <polygon points="112,43 120,43 149,0 141,0" fill="#fff"/>
      <polygon points="411,43 419,43 448,0 440,0" fill="#fff"/>
    </svg>
    <div class="band__text"><span class="band__url">www.mapleroster.nz</span></div>
  </div>
</section>

<section class="card card--back" aria-label="Business card back">
  <div class="social">
    <span class="social__dot social__dot--mail"></span>
    <span class="social__dot social__dot--network"></span>
  </div>

  <div class="person">
    <div class="person__name">Harriet Lowell</div>
    <div class="person__role">Director | Senior Search Consultant</div>
  </div>

  <ul class="contacts">
    <li>
      <svg viewBox="0 0 20 20" aria-hidden="true"><circle cx="10" cy="10" r="9" fill="none" stroke="var(--ink)" stroke-width="1.3"/><path d="M7 5.5l1.6 2.2-1 1.2c.6 1.3 1.6 2.3 2.8 2.9l1.2-1 2.2 1.6-.9 1.6c-3.3-.3-6.4-3.4-6.7-6.8z" fill="var(--ink)"/></svg>
      <span>+64 27 555 0142</span>
    </li>
    <li>
      <svg viewBox="0 0 20 20" aria-hidden="true"><circle cx="10" cy="10" r="9" fill="none" stroke="var(--ink)" stroke-width="1.3"/><path d="M10 4.5a3.5 3.5 0 0 0-3.5 3.5c0 2.6 3.5 6.5 3.5 6.5s3.5-3.9 3.5-6.5A3.5 3.5 0 0 0 10 4.5z" fill="none" stroke="var(--ink)" stroke-width="1.4"/><circle cx="10" cy="8" r="1.2" fill="var(--ink)"/></svg>
      <span>Kauri Bay, New Zealand's<br>North Island</span>
    </li>
    <li>
      <svg viewBox="0 0 20 20" aria-hidden="true"><circle cx="10" cy="10" r="9" fill="none" stroke="var(--ink)" stroke-width="1.3"/><rect x="5.5" y="7" width="9" height="6.5" fill="var(--ink)"/><path d="M5.5 7l4.5 3.5L14.5 7" fill="none" stroke="#fff" stroke-width="1"/></svg>
      <span>harriet@mapleroster.nz</span>
    </li>
    <li>
      <svg viewBox="0 0 20 20" aria-hidden="true"><circle cx="10" cy="10" r="9" fill="none" stroke="var(--ink)" stroke-width="1.3"/><circle cx="10" cy="10" r="4.5" fill="none" stroke="var(--ink)" stroke-width="1.2"/><path d="M5.5 10h9M10 5.5c-1.8 2.5-1.8 6.5 0 9M10 5.5c1.8 2.5 1.8 6.5 0 9" fill="none" stroke="var(--ink)" stroke-width="0.9"/></svg>
      <span>www.mapleroster.nz</span>
    </li>
  </ul>

  <div class="wordmark">MAPLE ROSTER</div>

  <div class="band">
    <svg viewBox="0 0 560 54" preserveAspectRatio="none" aria-hidden="true">
      <rect width="560" height="54" fill="var(--ink)"/>
      <polygon points="34,54 42,54 80,0 72,0" fill="#fff"/>
      <polygon points="492,54 500,54 538,0 530,0" fill="#fff"/>
    </svg>
    <div class="band__text">
      <span class="band__sector">Construction &amp; Property Developement</span>
      <span class="band__kind">CONSULTANCY</span>
    </div>
  </div>
</section>

</body>
</html>
```